Chartered Professional Accounting Firm Needs a Business Card Design

We need a card design for an accounting firm based in Toronto, Ontario. The firm name is Pavel Ostrom Professional Corporation. The owner of the firm is a chartered professional accountant and a certified general accountant. Services of the firm include 60% tax preparation and consulting and 40% financial statements for corporation year-end. We would like a modern design. The color could be black, white, gray, blue or other color to bring more confidence to clients. The logo of the firm should be included in the design. Thanks

Name: Pavel Ostrom, CPA, CGA Address: 47 Maple Crest Rd. Richmond Hill, ON L7K 3B5 Telephone: (416) 562-3907 Fax:(416) 734-2165 Email: pavel@pavelostrom-example.ca

Accounting

```html
<!DOCTYPE html>
<html lang="en">
<head>
<meta charset="utf-8">
<title>Pavel Ostrom Professional Corporation — Business Card</title>
<link rel="stylesheet" href="https://fonts.googleapis.com/css2?family=Marcellus&display=swap">
<style>
  :root {
    --backdrop: #e4e4e6;
    --card-white: #ffffff;
    --brand-blue: #2a2a8c;
    --brand-blue-deep: #1f1f73;
    --ink-gray: #8a8a95;
    --bevel-gray: #b9b9c2;
    --watermark: #e3e3ec;
    --on-blue: #e8e8f6;
  }
  * { box-sizing: border-box; margin: 0; padding: 0; }
  html, body { width: 1200px; height: 871px; overflow: hidden; }
  body {
    background: var(--backdrop);
    font-family: "Marcellus", serif;
    position: relative;
  }
  .card {
    position: absolute;
    width: 560px;
    height: 320px;
    background: var(--card-white);
    box-shadow: 0 6px 22px rgba(0,0,0,0.18);
    overflow: hidden;
  }
  .card--front { left: 110px; top: 80px; }
  .card--back  { left: 530px; top: 470px; }

  .brand { display: flex; align-items: center; gap: 10px; }
  .brand__mark {
    width: 34px; height: 34px;
    background: var(--brand-blue);
    flex: none;
  }
  .brand__text { color: var(--brand-blue); line-height: 1.05; }
  .brand__name { font-size: 25px; letter-spacing: 0.5px; text-transform: uppercase; }
  .brand__corp { font-size: 11.5px; letter-spacing: 1.2px; text-transform: uppercase; }
  .brand__designations {
    margin-top: 3px;
    font-size: 8.5px; letter-spacing: 1px; text-transform: uppercase;
    color: var(--ink-gray); line-height: 1.25;
  }

  .card--front .brand { position: absolute; left: 232px; top: 168px; }

  .back__left { position: absolute; inset: 0 auto 0 0; width: 262px; }
  .back__left .brand { position: absolute; left: 18px; top: 16px; }
  .back__left .brand__name { font-size: 20px; }
  .back__left .brand__corp { font-size: 9.5px; }
  .back__left .brand__designations { font-size: 7px; }
  .back__watermark {
    position: absolute; left: 70px; top: 110px;
    width: 150px; height: 170px;
    background: var(--watermark);
  }
  .back__right {
    position: absolute; top: 0; right: 0; bottom: 0; left: 270px;
    background: linear-gradient(160deg, var(--brand-blue) 0%, var(--brand-blue-deep) 100%);
    border-left: 8px solid var(--bevel-gray);
    color: var(--on-blue);
    padding: 48px 28px 0 20px;
    text-align: right;
  }
  .holder {
    font-size: 15px; letter-spacing: 3px; text-transform: uppercase;
    text-align: left;
  }
  .address {
    margin-top: 26px; font-size: 12px; letter-spacing: 1.5px; line-height: 1.7;
  }
  .contact { margin-top: 22px; list-style: none; font-size: 12px; letter-spacing: 1.5px; }
  .contact li { display: flex; justify-content: flex-end; align-items: center; gap: 14px; line-height: 1.9; }
  .contact svg { width: 14px; height: 14px; flex: none; }
</style>
</head>
<body>

  <section class="card card--front" aria-label="Business card front">
    <div class="brand">
      <span class="brand__mark"></span>
      <div class="brand__text">
        <div class="brand__name">Pavel Ostrom</div>
        <div class="brand__corp">Professional Corporation</div>
        <div class="brand__designations">Chartered Professional Accountant<br>Certified General Accountant</div>
      </div>
    </div>
  </section>

  <section class="card card--back" aria-label="Business card back">
    <div class="back__left">
      <div class="brand">
        <span class="brand__mark" style="width:26px;height:26px"></span>
        <div class="brand__text">
          <div class="brand__name">Pavel Ostrom</div>
          <div class="brand__corp">Professional Corporation</div>
          <div class="brand__designations">Chartered Professional Accountant<br>Certified General Accountant</div>
        </div>
      </div>
      <div class="back__watermark" aria-hidden="true"></div>
    </div>

    <div class="back__right">
      <p class="holder">Pavel Ostrom, CPA, CGA</p>
      <p class="address">47 Maple Crest Rd.<br>Richmond Hill,<br>ON L7K 3B5</p>
      <ul class="contact">
        <li>(416) 562-3907
          <svg viewBox="0 0 16 16" aria-label="Telephone"><path fill="currentColor" d="M2 6c0-2 2-3 6-3s6 1 6 3v1h-3V6H5v1H2zM4 8h8l1 5H3z"/></svg>
        </li>
        <li>(416) 734-2165
          <svg viewBox="0 0 16 16" aria-label="Fax"><path fill="none" stroke="currentColor" stroke-width="1.3" d="M4 6V2h8v4M2 6h12v6h-2M4 12H2V6M4 10h8v4H4z"/></svg>
        </li>
        <li>pavel@pavelostrom-example.ca
          <svg viewBox="0 0 16 16" aria-label="Email"><path fill="none" stroke="currentColor" stroke-width="1.3" d="M1.5 3.5h13v9h-13zM1.5 3.5l6.5 5 6.5-5"/></svg>
        </li>
      </ul>
    </div>
  </section>

</body>
</html>
```